MRT Property - Business Cards

Looking for a business card & general letterhead, signage etc design for our new logo.

Colours:
000a20
0056a2
00b5ef
0088ce
68cef2

Fonts:
Poppins
Karla

Please keep look and feel of new brand - example in the zip package I sent.

```html
<!DOCTYPE html>
<html lang="en">
<head>
<meta charset="UTF-8">
<title>MRT Property – Business Cards</title>
<link href="https://fonts.googleapis.com/css2?family=Poppins:wght@400;600;700&family=Karla:wght@400;500&display=swap" rel="stylesheet">
<style>
  :root {
    --navy: #000a20;
    --blue: #0056a2;
    --sky: #00b5ef;
    --mid: #0088ce;
    --pale: #68cef2;
    --stage: #3b3b3d;
    --paper: #ffffff;
    --ink: #3a3a3a;
    --rule: #cfd4da;
  }
  * { margin: 0; padding: 0; box-sizing: border-box; }
  html, body { width: 1200px; height: 689px; overflow: hidden; background: var(--stage); }
  .canvas { position: relative; width: 1200px; height: 689px; }

  .card {
    position: absolute;
    top: 200px;
    width: 500px;
    height: 286px;
    border-radius: 14px;
    overflow: hidden;
  }

  /* Back of card */
  .card-back { left: 70px; background: var(--blue); }
  .card-back .pattern-area {
    position: absolute; inset: 0;
    background: linear-gradient(135deg, #0a3f93 0%, var(--blue) 45%, var(--mid) 80%, var(--sky) 100%);
  }
  .card-back .back-name {
    position: absolute; right: 26px; top: 108px;
    font-family: "Poppins", sans-serif; font-weight: 600; font-size: 15px;
    color: var(--paper);
  }

  /* Front of card */
  .card-front { left: 630px; background: var(--paper); }
  .brand {
    position: absolute; right: 28px; top: 34px;
    display: flex; align-items: center; gap: 12px;
  }
  .brand-dot { width: 34px; height: 34px; border-radius: 50%; background: var(--mid); }
  .brand-name {
    font-family: "Poppins", sans-serif; font-weight: 700; font-size: 32px;
    color: var(--blue); letter-spacing: -0.5px; line-height: 1;
  }
  .divider {
    position: absolute; left: 28px; right: 28px; top: 112px;
    height: 1px; background: var(--rule);
  }
  .address {
    position: absolute; right: 28px; top: 124px; text-align: right;
    font-family: "Karla", sans-serif; font-size: 13px; line-height: 1.4; color: var(--ink);
  }
  .person { position: absolute; left: 28px; top: 138px; }
  .person-name {
    font-family: "Poppins", sans-serif; font-weight: 700; font-size: 21px;
    color: var(--blue); line-height: 1.1;
  }
  .person-role {
    font-family: "Karla", sans-serif; font-size: 13px; color: var(--sky);
  }
  .contact-list {
    position: absolute; left: 28px; top: 194px; list-style: none;
    font-family: "Karla", sans-serif; font-size: 12px; color: var(--ink);
    border-top: 1px solid var(--rule); padding-top: 4px; width: 160px;
  }
  .contact-list li { display: flex; align-items: center; gap: 7px; height: 15px; }
  .contact-list svg { width: 10px; height: 10px; fill: var(--blue); flex: none; }
  .band { position: absolute; left: 0; bottom: 0; width: 500px; height: 62px; }
  .web {
    position: absolute; right: 24px; bottom: 14px;
    font-family: "Karla", sans-serif; font-size: 12px; letter-spacing: 2px; color: var(--paper);
  }
</style>
</head>
<body>
<main class="canvas">

  <section class="card card-back">
    <div class="pattern-area" role="img" aria-label="Repeating brand symbol pattern in shades of blue"></div>
    <span class="back-name">MRT Property</span>
  </section>

  <section class="card card-front">
    <div class="brand">
      <span class="brand-dot"></span>
      <span class="brand-name">MRT Property</span>
    </div>
    <div class="divider"></div>

    <address class="address">1420 Harbor View Road<br>Halifax, Canada 30218</address>

    <div class="person">
      <div class="person-name">Daniel Reyes</div>
      <div class="person-role">President</div>
    </div>

    <ul class="contact-list">
      <li><svg viewBox="0 0 10 10"><path d="M2 0.5 L3.6 2.6 L2.8 3.6 Q4 6 6.4 7.2 L7.4 6.4 L9.5 8 L8.4 9.5 Q2.5 8.5 0.5 1.6 Z"/></svg>555-210-4487</li>
      <li><svg viewBox="0 0 10 10"><path d="M2.5 0 H7.5 V10 H2.5 Z M3.4 1 V8 H6.6 V1 Z"/></svg>555-318-9062</li>
      <li><svg viewBox="0 0 10 10"><path d="M0 2 H10 V8.5 H0 Z M0.8 2.6 L5 5.6 L9.2 2.6 Z" fill-rule="evenodd"/></svg>info@MRT.com</li>
    </ul>

    <svg class="band" viewBox="0 0 500 62" preserveAspectRatio="none" aria-hidden="true">
      <path d="M0 48 H326 L336 40 V26 L346 18 H500 V22 H350 L340 30 V44 L330 52 H0 Z" fill="var(--sky)"/>
      <path d="M0 56 H334 L344 48 V34 L354 26 H500 V62 H0 Z" fill="var(--blue)"/>
    </svg>
    <span class="web">www.MRT.com</span>
  </section>

</main>
</body>
</html>
```